770 76 Chiro Brochure

https://files.vornaledge.net/sheet/q/84TxRm_wLz-Kq_PYbnHcVe391zd_4RQlmJTsPAk92x6/view?src=link

Brochure to show chiropractors about our program

```html
<!DOCTYPE html>
<html lang="en">
<head>
<meta charset="utf-8">
<title>Chiropractic Billboard Program</title>
<link href="https://fonts.googleapis.com/css2?family=Roboto+Condensed:wght@300;400;700&family=Anton&family=Archivo+Black&family=Montserrat:wght@600;800&display=swap" rel="stylesheet">
<style>
:root{
  --yellow:#ffd200;
  --green:#6db33f;
  --black:#0b0b0b;
  --white:#ffffff;
  --red:#e1251b;
  --board:#10291a;
  --sky-top:#3f86d4;
  --sky-bottom:#cfe4f7;
  --ink:#161616;
}
*{box-sizing:border-box;margin:0;padding:0}
html,body{width:927px;height:1200px;overflow:hidden;background:var(--white)}
.flyer{position:relative;width:927px;height:1200px;overflow:hidden;font-family:"Roboto Condensed",sans-serif;background:var(--black)}
.sky{position:absolute;left:0;top:0;width:927px;height:460px;background:linear-gradient(180deg,var(--sky-top) 0%,#8dbde9 55%,var(--sky-bottom) 100%)}
.hero-photo{position:absolute;left:418px;top:18px;width:509px;height:420px;border-radius:6px;background:linear-gradient(180deg,#1f3b27 0%,#2f4a36 45%,#7f8a8f 75%,#b9c6d0 100%);opacity:.92}
.wave{position:absolute;left:0;top:340px;width:927px;height:130px}
.title{position:absolute;left:78px;top:92px;font-weight:700;font-size:53px;line-height:52px;color:var(--ink);letter-spacing:.5px}
.pill{position:absolute;left:0;top:254px;width:378px;height:47px;background:var(--yellow);border-radius:0 24px 24px 0;padding-left:78px;font-weight:700;font-size:33px;line-height:47px;color:var(--ink)}
.tagline{position:absolute;left:78px;top:312px;font-size:14.5px;color:var(--ink)}
.section-heading{position:absolute;left:80px;color:var(--yellow);font-weight:700}
.h-dominate{top:396px;font-size:35px;line-height:40px}
.h-includes{top:672px;font-size:39px;line-height:44px}
.checks{position:absolute;left:80px;top:490px;width:800px;list-style:none}
.checks li{position:relative;padding-left:32px;color:var(--white);font-weight:700;font-size:17.4px;line-height:20px}
.checks li + li{margin-top:18px}
.checks li:nth-child(3){margin-top:20px}
.checks svg{position:absolute;left:2px;top:1px;width:20px;height:18px}
.divider{position:absolute;width:5px;background:var(--black);top:728px;height:192px}
.feature{position:absolute;top:722px;display:flex;align-items:center;z-index:2}
.feature .badge{width:73px;height:73px;border-radius:50%;background:var(--green);display:flex;align-items:center;justify-content:center}
.feature .badge svg{width:46px;height:46px}
.feature p{margin-left:17px;color:var(--white);font-weight:700;font-size:18.5px;line-height:22px;letter-spacing:.3px;white-space:nowrap}
.f-photo{left:85px}.f-brand{left:268px}.f-dial{left:582px}
.panel{position:absolute;top:810px;height:222px}
.panel-yellow{left:0;width:460px;background:var(--yellow)}
.panel-green{left:460px;width:467px;background:var(--green)}
.stripe{position:absolute;top:0;height:180px;width:6px}
.panel-yellow .stripe{left:33px;background:var(--green)}
.panel-green .stripe{left:11px;background:var(--yellow)}
.panel h2{position:absolute;top:20px;font-weight:700;font-size:21.5px;color:var(--ink);white-space:nowrap}
.panel-yellow h2{left:62px}
.panel-green h2{left:39px}
.panel h2 small{font-weight:300;font-size:14.5px}
.panel .body{position:absolute;top:54px;font-weight:300;font-size:15.4px;line-height:18.2px;color:var(--ink)}
.panel-yellow .body{left:62px;width:378px}
.panel-yellow .body p + p{margin-top:18px}
.panel-green .body{left:40px;width:410px}
.boards{position:absolute;top:1043px;left:26px;display:flex;gap:4px}
.mini{position:relative;width:217px;height:77px;background:var(--board);border:2px solid var(--white);overflow:hidden;color:var(--white)}
.mini .photo{position:absolute;right:0;top:0;width:56px;height:75px;background:linear-gradient(180deg,#c9c3bd 0%,#8a7a8e 100%)}
.mini .hit{position:absolute;left:6px;top:3px;font-family:"Anton",sans-serif;font-size:10px;letter-spacing:.2px;white-space:nowrap}
.mini .hit b{font-weight:400;color:var(--red);font-size:16px}
.mini .call{position:absolute;left:6px;top:23px;font-family:"Montserrat",sans-serif;font-weight:800;font-size:7.5px;line-height:7.5px;color:var(--yellow)}
.mini .num{position:absolute;left:36px;top:20px;font-family:"Anton",sans-serif;font-size:19px;line-height:22px}
.mini .sub{position:absolute;left:6px;top:44px;font-family:"Montserrat",sans-serif;font-weight:600;font-size:4.6px;letter-spacing:.2px;white-space:nowrap}
.mini .bar{position:absolute;left:56px;top:52px;height:11px;padding:0 8px;background:var(--yellow);color:var(--ink);font-family:"Montserrat",sans-serif;font-weight:800;font-size:7px;line-height:11px}
.mini .brand{position:absolute;left:6px;top:56px;font-weight:700;font-size:9px;color:var(--white)}
.mini .docs{position:absolute;left:56px;top:66px;font-family:"Montserrat",sans-serif;font-weight:800;font-size:3.6px;white-space:nowrap}
.footer{position:absolute;left:26px;top:1128px;display:flex;align-items:center;white-space:nowrap}
.footer .cta{color:var(--yellow);font-weight:700;font-size:29px}
.footer .phone{margin-left:10px;color:var(--white);font-family:"Archivo Black",sans-serif;font-size:27px;letter-spacing:1px}
.footer .sep{margin:0 13px;width:1.5px;height:22px;background:#888}
.footer .web{color:var(--green);font-size:17px;letter-spacing:2.3px}
</style>
</head>
<body>
<main class="flyer">
  <div class="sky" role="img" aria-label="Blue sky with soft white clouds"></div>
  <div class="hero-photo" role="img" aria-label="Photo of a roadside billboard showing a car accident chiropractic ad with the doctor's portrait"></div>

  <h1 class="title">CHIROPRACTIC<br>BILLBOARD<br>PROGRAM</h1>
  <div class="pill">PERSONAL INJURY</div>
  <p class="tagline">WE PARTNER WITH GEORGIA CHIROPRACTORS.</p>

  <svg class="wave" viewBox="0 0 927 130" preserveAspectRatio="none" aria-hidden="true">
    <path d="M0 52 C150 16 300 22 470 66 S790 96 927 38 L927 130 L0 130 Z" fill="#6db33f"/>
    <path d="M0 60 C150 26 300 32 470 76 S790 104 927 50 L927 130 L0 130 Z" fill="#0b0b0b"/>
  </svg>

  <h2 class="section-heading h-dominate">How to Dominate<br>Personal Injury Advertising</h2>

  <ul class="checks">
    <li><svg viewBox="0 0 20 18"><path d="M2 10 L7 15 L18 2" fill="none" stroke="#ffd200" stroke-width="3.5" stroke-linecap="round" stroke-linejoin="round"/></svg>(555) 30-CHIRO is the preeminent vanity phone number for Chiropractors in Georgia to dominate personal injury advertising.</li>
    <li><svg viewBox="0 0 20 18"><path d="M2 10 L7 15 L18 2" fill="none" stroke="#ffd200" stroke-width="3.5" stroke-linecap="round" stroke-linejoin="round"/></svg>(555) 30-CHIRO is more valuable than ever because of digital advertising.</li>
    <li><svg viewBox="0 0 20 18"><path d="M2 10 L7 15 L18 2" fill="none" stroke="#ffd200" stroke-width="3.5" stroke-linecap="round" stroke-linejoin="round"/></svg>See how (555) 30-CHIRO proved to substantially increase ROI through the Searchwell Ads Algorithm and increase your Searchwell Quality Score.</li>
  </ul>

  <h2 class="section-heading h-includes">Every Billboard we create includes</h2>

  <section class="panel panel-yellow">
    <span class="stripe"></span>
    <h2>Reach New Clients / Patients in a Big Way!</h2>
    <div class="body">
      <p>Expand your marketing mix and grow your business through our professionally designed billboards that showcase your photo, name, logo, at any time and in any place.</p>
      <p>Billboards set you apart from the competition by building credibility and brand recognition. Billboards serve as an important top-of-funnel channel and in conjunction with your current marketing channels, will increase your effectiveness.</p>
    </div>
  </section>
  <section class="panel panel-green">
    <span class="stripe"></span>
    <h2>Georgia Billboard Locations <small>(Over 200 Boards Available)</small></h2>
    <p class="body">Albany - Athens - Atlanta - Augusta - Blairville - Blackshear - Blue Ridge - Conyers - Valdosta Cummings- Dalton- Ft Oglethorpe - Hazelhurst - Jesup - Kennesaw - Macon - McDonough Savannah - Thomasville - Toccoa - Young Harris - Watkinsville - Bogart - Winder - Sandersville Tifton - Cordele - Clayton - Millidgeville - Dublin - Chatsworth- Mineral Bluff- Eatonsville Hinesville - Warner Robins - Moultrie - LaFayette - Senoia - Ackworth - Camilla - Dawsonville Barnesville - Bainbridge- Cairo - Americus</p>
  </section>
  <span class="divider" style="left:40px"></span>
  <span class="divider" style="left:478px"></span>

  <div class="feature f-photo">
    <div class="badge"><svg viewBox="0 0 46 46"><circle cx="23" cy="15" r="9" fill="#0b0b0b"/><path d="M6 44 C6 32 14 27 23 27 C32 27 40 32 40 44 Z" fill="#0b0b0b"/></svg></div>
    <p>DOCTORS<br>PHOTO</p>
  </div>
  <div class="feature f-brand">
    <div class="badge"><svg viewBox="0 0 46 46"><circle cx="23" cy="23" r="20" fill="none" stroke="#0b0b0b" stroke-width="3"/><text x="23" y="28" text-anchor="middle" font-family="Anton, sans-serif" font-size="14" fill="#0b0b0b">LOGO</text></svg></div>
    <p>YOUR BRAND /<br>LOGO ON THE BILLBOARDS</p>
  </div>
  <div class="feature f-dial">
    <div class="badge"><svg viewBox="0 0 46 46"><path d="M10 8 L17 7 L20 16 L15 19 C18 26 21 29 27 31 L30 26 L39 29 L38 36 C37 39 34 40 31 40 C18 38 8 28 6 15 C6 12 7 9 10 8 Z" fill="#0b0b0b"/><path d="M27 6 A13 13 0 0 1 40 19" fill="none" stroke="#0b0b0b" stroke-width="3"/><path d="M26 12 A7 7 0 0 1 34 20" fill="none" stroke="#0b0b0b" stroke-width="3"/></svg></div>
    <p>DIRECT DIAL FORWARDED<br>TO YOUR OFFICE</p>
  </div>

  <div class="boards">
    <article class="mini">
      <div class="photo" role="img" aria-label="Photo of two doctors in scrubs"></div>
      <div class="hit"><b>INJURED</b> IN A CAR ACCIDENT?</div>
      <div class="call">CALL<br>NOW</div><div class="num">(555) 30-CHIRO</div>
      <div class="sub">SAME DAY APPOINTMENTS | LOCATIONS ACROSS GEORGIA</div>
      <div class="brand">Oakline Chiro</div>
      <div class="bar">NECK &amp; BACK PAIN</div>
      <div class="docs">DR. LENA MARSH, D.C &amp; DR. OWEN BELL, D.C</div>
    </article>
    <article class="mini">
      <div class="photo" role="img" aria-label="Photo of a doctor in a white coat"></div>
      <div class="hit"><b>INJURED</b> IN A CAR ACCIDENT?</div>
      <div class="call">CALL<br>NOW</div><div class="num">(555) 30-CHIRO</div>
      <div class="sub">SAME DAY APPOINTMENTS | LOCATIONS ACROSS GEORGIA</div>
      <div class="brand">EasePath</div>
      <div class="bar" style="top:57px;left:64px">NECK &amp; BACK PAIN</div>
    </article>
    <article class="mini">
      <div class="photo" role="img" aria-label="Photo of a doctor in a white coat"></div>
      <div class="hit"><b>INJURED</b> IN A CAR ACCIDENT?</div>
      <div class="call">CALL<br>NOW</div><div class="num">(555) 30-CHIRO</div>
      <div class="sub">SAME DAY APPOINTMENTS | LOCATIONS ACROSS GEORGIA</div>
      <div class="brand">EasePath</div>
      <div class="bar" style="top:57px;left:64px">NECK &amp; BACK PAIN</div>
    </article>
    <article class="mini">
      <div class="photo" role="img" aria-label="Photo of a smiling doctor"></div>
      <div class="hit"><b>INJURED</b> IN A CAR ACCIDENT?</div>
      <div class="call">CALL<br>NOW</div><div class="num">(555) 30-CHIRO</div>
      <div class="sub">SAME DAY APPOINTMENTS | LOCATIONS ACROSS GEORGIA</div>
      <div class="brand">Redbud Chiro</div>
      <div class="bar" style="top:58px;left:64px">HABLA ESPANOL</div>
    </article>
  </div>

  <footer class="footer">
    <span class="cta">FOR MORE DETAIL CALL US NOW :</span>
    <span class="phone">1234 567 890</span>
    <span class="sep"></span>
    <span class="web">WWW.YOURWEBSITE.COM</span>
  </footer>
</main>
</body>
</html>
```